Informational Site for Advanced Chemistry R&D

The company develops oxidation chemistry for air, water, fuel pollution controls. The site has been prototyped at www.velquaresearch.example. Take a look. Now, the task is to design it for eye-catching beauty with use of color, on-page scroll-driven color transition and parallax effects. Should capture the themes: high technology, wow it's beautiful, modern, uncluttered, clean urban environment.

Target Market(s)

China Environmentally Conscious Government and Industry,

Industry/Entity Type

It Company

Number of Pages Required

3 page

Font styles to use
Sans Serif

Requirements
Must have
• Parallax effects, desktop compatible, Rich, Modern, Simple, Graphic
Nice to have
• Mobile Phone Compatible
Should not have
• Flash, or anything that is slow to load or requires high bandwidth

```html
<!DOCTYPE html>
<html lang="en">
<head>
<meta charset="utf-8">
<title>Velqua – Advanced Oxidation</title>
<link href="https://fonts.googleapis.com/css2?family=Lato:wght@400;700;900&family=Open+Sans:ital,wght@0,400;0,600;1,400&display=swap" rel="stylesheet">
<style>
:root{
  --teal:#2bbbb5;
  --blue:#1f6fb5;
  --blue-dark:#1a5e9c;
  --ink:#1d1d1d;
  --text:#333;
  --light-cyan:#eefbfc;
  --light-grey:#f1f1f1;
  --partners-bg:#4b4b4b;
  --footer-bg:#161616;
  --footer-bar:#0c0c0c;
  --white:#fff;
}
*{margin:0;padding:0;box-sizing:border-box}
html,body{width:1200px;height:2267px;overflow:hidden;background:var(--white)}
body{font-family:'Lato',sans-serif;color:var(--text);position:relative}
.page{position:relative;width:1200px;height:2267px}
.block{position:absolute;left:0;width:1200px}

/* header */
.site-header{top:0;height:103px;border-top:4px solid var(--teal);background:var(--white)}
.brand{position:absolute;left:126px;top:30px;display:flex;align-items:center;gap:10px}
.brand-dot{width:30px;height:30px;border-radius:50%;background:var(--teal)}
.brand-name{font-size:28px;font-weight:700;color:var(--blue)}
.main-nav{position:absolute;right:106px;top:0;height:99px;display:flex;gap:0}
.main-nav a{display:block;height:99px;line-height:110px;padding:0 11px;font-size:13px;font-weight:700;color:var(--ink);text-decoration:none;text-transform:uppercase;position:relative}
.main-nav a.active{color:var(--teal)}
.main-nav a.active::after{content:"";position:absolute;left:2px;right:2px;bottom:0;height:4px;background:var(--teal)}
.main-nav a.active::before{content:"";position:absolute;left:50%;top:-4px;margin-left:-5px;border:5px solid transparent;border-top-color:var(--teal)}

/* hero */
.hero{top:103px;height:505px;background:linear-gradient(180deg,#8c9298 0%,#b6babd 45%,#9da2a6 100%)}
.hero-scene{position:absolute;inset:0;background:
  radial-gradient(ellipse 420px 260px at 870px 230px,rgba(240,240,240,.85),transparent 70%),
  radial-gradient(ellipse 300px 200px at 420px 130px,rgba(225,225,225,.7),transparent 70%),
  linear-gradient(90deg,transparent 318px,#a94a3f 318px,#a94a3f 345px,transparent 345px),
  linear-gradient(180deg,transparent 60%,#3e4448 100%)}
.welcome{position:absolute;left:343px;top:174px;width:509px;height:139px;background:rgba(235,235,235,.82);text-align:center;color:#333}
.welcome h1{font-size:36px;font-weight:700;margin-top:24px;letter-spacing:.5px}
.welcome p{font-size:19px;line-height:21px;margin-top:6px}
.slider-dots{position:absolute;left:576px;top:480px;display:flex;gap:4px}
.slider-dots span{width:10px;height:10px;border-radius:50%;background:#555}
.slider-dots span.on{width:13px;height:13px;margin-top:-1.5px;background:#fff}

/* section titles */
.section-title{text-align:center;font-size:21px;font-weight:700;color:var(--blue);text-transform:uppercase}
.wave{display:block;margin:4px auto 0}

/* ideas */
.ideas{top:608px;height:369px}
.ideas .section-title{margin-top:47px}
.ideas-lead{text-align:center;font-size:15px;color:#222;margin-top:18px}
.pillars{position:absolute;top:172px;left:0;width:1200px}
.pillar{position:absolute;width:180px;margin-left:-90px;text-align:center}
.pillar-icon{width:120px;height:120px;margin:0 auto;border-radius:50%;background:#eeeeee;display:flex;align-items:center;justify-content:center}
.pillar-icon.featured{background:var(--teal);box-shadow:0 0 0 12px #fff,0 0 0 22px #a9cfe8}
.pillar-label{font-size:17px;font-weight:700;color:var(--ink);margin-top:22px}

/* advanced oxidation */
.oxidation{top:977px;height:343px;display:flex}
.oxidation-copy{width:598px;background:var(--light-cyan);padding:45px 0 0 101px}
.oxidation-copy h2{font-size:21px;font-weight:700;color:var(--blue);text-transform:uppercase}
.oxidation-copy .wave{margin:3px 0 0 75px}
.oxidation-copy p,.oxidation-copy li{font-family:'Open Sans',sans-serif;font-size:11.5px;line-height:24px;color:var(--blue-dark)}
.oxidation-copy p:first-of-type{margin-top:8px;width:460px}
.oxidation-copy ul{list-style:none}
.oxidation-copy li{padding-left:12px;position:relative}
.oxidation-copy li::before{content:"";position:absolute;left:1px;top:9px;border:3px solid transparent;border-left:4px solid var(--blue-dark)}
.btn{display:inline-block;background:var(--blue);color:#fff;font-size:12px;font-weight:700;text-transform:uppercase;padding:0 17px;height:33px;line-height:33px;margin-top:32px;letter-spacing:.3px}
.oxidation-figure{flex:1;background:var(--light-grey);position:relative}
.oxidation-figure .diagram{position:absolute;left:95px;top:20px;width:290px;height:310px;border-radius:50%;background:radial-gradient(circle at 50% 48%,#f7cd2e 0 24px,#fbe9a2 25px,#f4f0e4 95px,var(--light-grey) 150px)}

/* solutions */
.solutions{top:1320px;height:368px}
.solutions .section-title{margin-top:42px}
.solution-grid{position:absolute;top:112px;left:98px;display:flex;gap:31px}
.solution{width:227px}
.solution-photo{height:171px}
.photo-refinery{background:linear-gradient(180deg,#8e959a,#3d4449)}
.photo-worker{background:linear-gradient(180deg,#b8b4aa,#3e5170)}
.photo-stacks{background:linear-gradient(180deg,#3c3f55,#6d6c78 70%,#2a2b30)}
.photo-outfall{background:linear-gradient(180deg,#6c8a4c,#9b8a5c 60%,#7a6a46)}
.solution-label{height:45px;line-height:47px;background:var(--teal);color:#fff;font-size:13px;font-weight:700;text-transform:uppercase;padding-left:7px;white-space:nowrap}

/* partners */
.partners{top:1688px;height:256px;background:var(--partners-bg)}
.partners .section-title{color:#fff;margin-top:29px}
.partner-row{position:absolute;top:93px;left:160px;display:flex;gap:51px}
.partner{width:182px;height:118px;background:#fff;display:flex;align-items:center;justify-content:center;gap:8px}
.partner .brand-name{font-size:24px}
.partner .brand-dot{width:22px;height:22px}
.badge{width:64px;height:64px;border-radius:50%}
.badge-red{border:3px solid #b52a3a}
.badge-blue{border:3px solid #2f6ea0}
.badge-gold{border-radius:8px;background:#e4b638}

/* footer */
.site-footer{top:1944px;height:276px;background:var(--footer-bg);color:#fff}
.footer-brand{position:absolute;left:127px;top:62px;display:flex;align-items:center;gap:8px}
.footer-brand .brand-dot{background:#fff;width:24px;height:24px}
.footer-brand .brand-name{color:#fff;font-size:24px}
.footer-heading{font-size:17px;font-weight:700;position:absolute;top:33px}
.contacts{position:absolute;left:333px;top:0;width:200px}
.contacts ul{list-style:none;position:absolute;top:74px;left:0;width:200px}
.contacts li{font-family:'Open Sans',sans-serif;font-size:11.5px;line-height:18px;display:flex;gap:10px;margin-bottom:9px}
.contacts svg{flex:none;margin-top:2px}
.enquiry{position:absolute;left:548px;top:0;width:362px}
.field{position:absolute;background:#fff;border-radius:3px;font-family:'Open Sans',sans-serif;font-style:italic;font-size:12.5px;color:#444;padding:0 14px;line-height:33px;height:33px}
.submit{position:absolute;left:2px;top:229px;width:107px;height:35px;background:var(--blue);font-size:13px;font-weight:700;text-align:center;line-height:35px;text-transform:uppercase}
.follow{position:absolute;left:963px;top:0}
.social{position:absolute;top:74px;left:0;display:flex;gap:7px}
.social span{width:24px;height:24px;border-radius:3px;background:#4d79b0;display:flex;align-items:center;justify-content:center}
.social span.mail{background:#e8e8e8}
.footer-bar{top:2220px;height:47px;background:var(--footer-bar);color:#ddd}
.footer-nav{position:absolute;left:102px;top:0;display:flex;gap:20px}
.footer-nav a{font-size:10.5px;line-height:47px;color:#ddd;text-decoration:none;text-transform:uppercase}
.copyright{position:absolute;left:916px;line-height:47px;font-family:Arial,sans-serif;font-size:10.5px}
</style>
</head>
<body>
<div class="page">

<header class="block site-header">
  <div class="brand"><span class="brand-dot"></span><span class="brand-name">Velqua</span></div>
  <nav class="main-nav">
    <a class="active" href="#">Home</a>
    <a href="#">Technology</a>
    <a href="#">Products</a>
    <a href="#">Contact Us</a>
  </nav>
</header>

<section class="block hero">
  <div class="hero-scene" role="img" aria-label="Industrial smokestacks releasing white plumes into a grey sky"></div>
  <div class="welcome">
    <h1>WELCOME</h1>
    <p>Advanced Oxidation<br>Science for Environmental Pollution Management</p>
  </div>
  <div class="slider-dots"><span class="on"></span><span></span><span></span></div>
</section>

<section class="block ideas">
  <h2 class="section-title">New Ideas for a Cleaner World</h2>
  <svg class="wave" width="72" height="14" viewBox="0 0 72 14"><path d="M2 5 Q20 0 36 5 T70 5" fill="none" stroke="#1f6fb5" stroke-width="2.5"/><path d="M2 11 Q20 6 36 11 T70 11" fill="none" stroke="#1f6fb5" stroke-width="1.5"/></svg>
  <p class="ideas-lead">Environmental pollution control solutions employing nature's most reactive Free Radical</p>
  <div class="pillars">
    <div class="pillar" style="left:282px">
      <div class="pillar-icon featured">
        <svg width="28" height="36" viewBox="0 0 28 36"><path d="M14 2 C10 12 3 18 3 24 a11 11 0 0 0 22 0 C25 18 18 12 14 2Z" fill="#fff"/></svg>
      </div>
      <div class="pillar-label">WATER</div>
    </div>
    <div class="pillar" style="left:609px">
      <div class="pillar-icon">
        <svg width="40" height="40" viewBox="0 0 40 40"><path d="M20 21 a3 3 0 1 1 4 -3 a7 7 0 1 1 -9 -6 a12 12 0 1 1 -2 22 l8 0" fill="none" stroke="#111" stroke-width="3.5" stroke-linecap="round"/></svg>
      </div>
      <div class="pillar-label">AIR</div>
    </div>
    <div class="pillar" style="left:925px">
      <div class="pillar-icon">
        <svg width="40" height="44" viewBox="0 0 40 44"><rect x="4" y="4" width="22" height="36" rx="3" fill="#111"/><rect x="8" y="9" width="14" height="10" fill="#eee"/><path d="M26 16 h5 v18 a3 3 0 0 0 6 0 V14 l-5 -6" fill="none" stroke="#111" stroke-width="3"/></svg>
      </div>
      <div class="pillar-label">FUEL</div>
    </div>
  </div>
</section>

<section class="block oxidation">
  <div class="oxidation-copy">
    <h2>Advanced Oxidation</h2>
    <svg class="wave" width="72" height="14" viewBox="0 0 72 14"><path d="M2 5 Q20 0 36 5 T70 5" fill="none" stroke="#1f6fb5" stroke-width="2.5"/><path d="M2 11 Q20 6 36 11 T70 11" fill="none" stroke="#1f6fb5" stroke-width="1.5"/></svg>
    <p>Advanced Oxidation refers to a variety of techniques employing the Hydroxyl Radical, an energetic, highly reactive cousin of the water molecule:</p>
    <ul>
      <li>To add oxygen to inorganic molecules</li>
      <li>To remove hydrogen from organic molecules</li>
    </ul>
    <p>These transformations convert important industrial contaminants into reactive forms that can be captured or that disintegrate into harmless end products.</p>
    <span class="btn">Read More</span>
  </div>
  <div class="oxidation-figure">
    <div class="diagram" role="img" aria-label="Reaction diagram of the hydroxyl radical at the centre, linked by arrows to the molecules it reacts with"></div>
  </div>
</section>

<section class="block solutions">
  <h2 class="section-title">Solutions</h2>
  <svg class="wave" width="72" height="14" viewBox="0 0 72 14"><path d="M2 5 Q20 0 36 5 T70 5" fill="none" stroke="#1f6fb5" stroke-width="2.5"/><path d="M2 11 Q20 6 36 11 T70 11" fill="none" stroke="#1f6fb5" stroke-width="1.5"/></svg>
  <div class="solution-grid">
    <div class="solution"><div class="solution-photo photo-refinery" role="img" aria-label="Oil refinery towers and pipework"></div><div class="solution-label">Fuel Oil Desulfurization</div></div>
    <div class="solution"><div class="solution-photo photo-worker" role="img" aria-label="Worker in a respirator handling chemical drums"></div><div class="solution-label">Volatile Organic Compunds</div></div>
    <div class="solution"><div class="solution-photo photo-stacks" role="img" aria-label="Power plant stacks emitting dark smoke"></div><div class="solution-label">Flue Gas Scrubbing</div></div>
    <div class="solution"><div class="solution-photo photo-outfall" role="img" aria-label="Wastewater pouring from an outfall pipe into a stream"></div><div class="solution-label">Wastewater Treatment</div></div>
  </div>
</section>

<section class="block partners">
  <h2 class="section-title">Partners</h2>
  <svg class="wave" width="72" height="14" viewBox="0 0 72 14"><path d="M2 5 Q20 0 36 5 T70 5" fill="none" stroke="#fff" stroke-width="2.5"/><path d="M2 11 Q20 6 36 11 T70 11" fill="none" stroke="#fff" stroke-width="1.5"/></svg>
  <div class="partner-row">
    <div class="partner"><span class="brand-dot"></span><span class="brand-name">Velqua</span></div>
    <div class="partner"><span class="badge badge-red"></span></div>
    <div class="partner"><span class="badge badge-blue"></span></div>
    <div class="partner"><span class="badge badge-gold"></span></div>
  </div>
</section>

<footer class="block site-footer">
  <div class="footer-brand"><span class="brand-dot"></span><span class="brand-name">Velqua</span></div>
  <div class="contacts">
    <h3 class="footer-heading">Contacts</h3>
    <ul>
      <li><svg width="9" height="12" viewBox="0 0 9 12"><path d="M4.5 0a4.5 4.5 0 0 0-4.5 4.5C0 8 4.5 12 4.5 12S9 8 9 4.5A4.5 4.5 0 0 0 4.5 0zm0 6.3a1.8 1.8 0 1 1 0-3.6 1.8 1.8 0 0 1 0 3.6z" fill="#fff"/></svg><span>Velqua Research Corporation<br>Harlow Creek, New Jersey, U.S.A.</span></li>
      <li><svg width="11" height="11" viewBox="0 0 11 11"><path d="M2 0l2 2.5-1.2 1.4a7 7 0 0 0 4.3 4.3L8.5 7 11 9l-1.5 2C4.5 11 0 6.5 0 1.5z" fill="#fff"/></svg><span>+1 555 014 2290</span></li>
      <li><svg width="12" height="9" viewBox="0 0 12 9"><rect width="12" height="9" fill="#fff"/><path d="M0 0l6 5 6-5" fill="none" stroke="#161616" stroke-width="1.2"/></svg><span>info@velquaresearch.example</span></li>
    </ul>
  </div>
  <div class="enquiry">
    <h3 class="footer-heading">Quick Enquiry</h3>
    <div class="field" style="left:2px;top:74px;width:172px">First Name:</div>
    <div class="field" style="left:192px;top:74px;width:172px">Last Name:</div>
    <div class="field" style="left:2px;top:118px;width:172px">Email:</div>
    <div class="field" style="left:192px;top:118px;width:172px">Phone:</div>
    <div class="field" style="left:2px;top:162px;width:362px;height:46px;line-height:44px">Message:</div>
    <div class="submit">Submit</div>
  </div>
  <div class="follow">
    <h3 class="footer-heading">Follow Us</h3>
    <div class="social">
      <span aria-label="Social profile"></span>
      <span aria-label="Social profile" style="background:#4a9ccf"></span>
      <span aria-label="Social profile" style="background:#3f6fa8"></span>
      <span class="mail" aria-label="Email"><svg width="16" height="11" viewBox="0 0 16 11"><rect x=".5" y=".5" width="15" height="10" fill="#fff" stroke="#999"/><path d="M.5 .5l7.5 6 7.5-6" fill="none" stroke="#999"/></svg></span>
    </div>
  </div>
</footer>

<div class="block footer-bar">
  <nav class="footer-nav"><a href="#">Home</a><a href="#">Technology</a><a href="#">Products</a><a href="#">Contact Us</a></nav>
  <span class="copyright">Copyright© 2016. All Rights Reserved.</span>
</div>

</div>
</body>
</html>
```